The Closed Circle News Report

This is a professional and academic report of 35 pages for journalists and teachers. The topic of the report is News Sharing: journalism, social networks and technology. Attached there is an example of the kind of design we are looking for: visual, fresh and modern.

Target Market(s)

Journalists, Journalism Students, Communication Researchers,

Industry/Entity Type

Media

Font styles to use
Sans Serif

Colors
3276b5
33a6d7
886aae
b868aa

Requirements
Must have
• Copyleft images, visual style
Nice to have
• There is an example attached.

```html
<!DOCTYPE html>
<html lang="en">
<head>
<meta charset="utf-8">
<title>The Closed Circle News Report</title>
<link rel="stylesheet" href="https://fonts.googleapis.com/css2?family=Arimo:wght@400;700&family=Tinos:ital,wght@0,400;0,700;1,400&display=swap">
<style>
  :root{
    --purple:#886aae;
    --pink:#b868aa;
    --blue:#3276b5;
    --cyan:#33a6d7;
    --teal:#2b6e88;
    --red:#c8232c;
    --ink:#333;
    --muted:#555;
    --paper:#ffffff;
    --stage:#8e98a6;
    --sans:"Arimo", Arial, sans-serif;
    --serif:"Tinos", "Times New Roman", serif;
  }
  *{box-sizing:border-box;margin:0;padding:0}
  html,body{width:1200px;height:800px;overflow:hidden}
  body{background:var(--stage);position:relative;font-family:var(--serif);color:var(--ink)}

  /* ---------- Cover ---------- */
  .cover{position:absolute;left:40px;top:160px;width:340px;height:480px;background:var(--paper);overflow:hidden}
  .cover__head{height:135px;background:var(--purple);padding:30px 24px 0;color:#fff;font-family:var(--sans)}
  .cover__title{font-size:29px;font-weight:700;line-height:1.08}
  .cover__subtitle{font-size:13px;margin-top:6px}
  .cover__photo{height:210px;background:linear-gradient(135deg,#5a4030 0%,#8a6a50 45%,#c9bfc4 60%,#6d5040 100%)}
  .cover__foot{height:135px;background:var(--purple);color:#fff;text-align:center;padding:22px 18px 0}
  .cover__credit{font-style:italic;font-size:9.5px;line-height:1.35}
  .cover__year{font-size:22px;margin-top:12px}

  /* ---------- Spread ---------- */
  .spread{position:absolute;left:410px;top:160px;width:750px;height:480px;display:flex}
  .page{position:relative;width:375px;height:480px;background:var(--paper);overflow:hidden}
  .page--left{border-right:1px solid #ddd}
  .page__curve{position:absolute;bottom:0;left:0;width:100%;height:90px}
  .page__num{position:absolute;bottom:10px;font-size:7px;color:#fff}

  .chapter-title{position:absolute;left:30px;top:56px;width:220px;height:46px;border:1px solid var(--red);padding:3px;font-weight:400}
  .chapter-title span{display:block;height:100%;border:1px solid var(--red);color:var(--red);font-size:19px;line-height:38px;padding-left:10px;white-space:nowrap}

  .columns{position:absolute;display:flex;gap:14px;font-size:7.5px;line-height:1.4;text-align:justify;color:var(--muted)}
  .columns p{flex:1}
  .columns--intro{left:30px;top:120px;width:315px}

  .quadrants{position:absolute;left:30px;top:205px;width:315px;height:200px;font-family:var(--sans)}
  .quadrants__axis{position:absolute;border-color:#999;border-style:dashed;border-width:0}
  .quadrants__axis--h{left:0;right:0;top:50%;border-top-width:1px}
  .quadrants__axis--v{top:0;bottom:0;left:50%;border-left-width:1px}
  .quadrants__label{position:absolute;font-family:var(--serif);font-size:6.5px;color:var(--muted);background:#fff;padding:0 2px}
  .quad-box{position:absolute;width:118px;height:66px;border:2px solid var(--teal);border-left:5px dotted var(--teal);background:#fff;padding:6px 8px;font-size:9px;font-weight:700;color:#222;line-height:1.1}
  .quad-box ul{list-style:none;font-weight:400;font-family:var(--serif);font-size:6.5px;line-height:1.25;margin-top:3px;color:var(--muted)}

  .running-head{position:absolute;left:30px;right:30px;top:20px;font-size:6.5px;color:var(--muted);display:flex;gap:4px}
  .running-head i{flex:1;border-bottom:1px dotted #999;margin-bottom:2px}
  .figure-caption{position:absolute;left:40px;top:34px;font-size:6.5px;color:var(--muted)}
  .figure-photo{position:absolute;left:40px;top:48px;width:290px;height:118px;background:linear-gradient(90deg,#b8b8b8,#8e8e8e 55%,#c4c4c4)}
  .columns--figure{left:40px;top:176px;width:290px}
  .lead{position:absolute;left:40px;top:222px;width:290px;font-size:7.5px;line-height:1.4;color:var(--muted)}
  .pull-quote{position:absolute;left:36px;top:250px;width:300px;border:1.5px solid var(--blue);border-radius:22px;padding:9px 16px;font-style:italic;font-size:8.5px;line-height:1.35;color:var(--blue)}
  .pull-quote cite{font-style:normal;font-size:7px}
  .columns--body{left:40px;top:318px;width:290px}
</style>
</head>
<body>

<section class="cover">
  <header class="cover__head">
    <h1 class="cover__title">The Closed Circle<br>News Report</h1>
    <p class="cover__subtitle">A starting guide for researchers and journalists</p>
  </header>
  <div class="cover__photo" role="img" aria-label="Photo from above of hands typing on a laptop on a wooden desk, with a coffee cup and a notebook"></div>
  <footer class="cover__foot">
    <p class="cover__credit">A report by Daniel Ortega Marín with the help of<br>Visiting Scholar at the Capital Hill University (Washington, D.C., USA)<br>Research Grants 18/19 from the Southern Coast University (Murcia, Spain)</p>
    <p class="cover__year">2019</p>
  </footer>
</section>

<section class="spread">
  <article class="page page--left">
    <h2 class="chapter-title"><span>1. The Media Landscape</span></h2>
    <div class="columns columns--intro">
      <p>If we think about the intersection of the online world and privacy, we can see in the following figure how this report is placed. Public channels shape the news we see, while private channels shape the news we trust and pass on to friends.</p>
      <p>That is always a sign. There is a growing body of private journalism in closed spaces, where sharing works in small circles such as family chats and group messages.</p>
    </div>

    <div class="quadrants">
      <span class="quadrants__axis quadrants__axis--h"></span>
      <span class="quadrants__axis quadrants__axis--v"></span>
      <span class="quadrants__label" style="left:0;top:-10px">1. OFFLINE / PUBLIC</span>
      <span class="quadrants__label" style="right:0;top:-10px">2. ONLINE / PUBLIC</span>
      <div class="quad-box" style="left:14px;top:14px">Traditional mass media</div>
      <div class="quad-box" style="left:178px;top:14px">Online media and social media</div>
      <div class="quad-box" style="left:14px;top:120px">Offline personal communication</div>
      <div class="quad-box" style="left:178px;top:112px;height:84px">Online private messaging:
        <ul><li>ChatLine</li><li>Circle Messenger</li><li>Text Messaging</li><li>Relay</li><li>Direct Messages</li><li>Etc.</li></ul>
      </div>
    </div>

    <svg class="page__curve" viewBox="0 0 375 90" preserveAspectRatio="none" aria-hidden="true">
      <path d="M0 30 C120 70 260 88 375 90 L0 90 Z" fill="var(--purple)"/>
    </svg>
    <span class="page__num" style="left:20px">6</span>
  </article>

  <article class="page page--right">
    <div class="running-head"><span>3. OFFLINE / PRIVATE</span><i></i><span>4. ONLINE / PRIVATE</span></div>
    <p class="figure-caption">Figure 1. The four quadrants of communication related to privacy and journalism.</p>
    <div class="figure-photo" role="img" aria-label="Black and white photo of a person holding a sheet with a question mark in front of their head"></div>
    <div class="columns columns--figure">
      <p>We could define "private journalism" as those practices, products and audiences that reach the public through closed messaging networks.</p>
      <p>Part of the trick is to offer more personalised experiences by looking into the small communities of readers.</p>
    </div>
    <p class="lead">This guide is designed to reach a particular profile of audience: those who are using or exploring private communication for news sharing.</p>
    <blockquote class="pull-quote">"I'd say we do share news on ChatLine but I think a lot of it would be a news article and then following that, for the next two weeks would be memes and a load of jokes but depending on the article" <cite>– Sam, 18 years old, UK.</cite></blockquote>
    <div class="columns columns--body">
      <p>The audience problem is not an isolated one for small outlets or startups, but it is worldwide. For instance, during an independent survey, many people said they read the news they get through messaging apps.</p>
      <p>When disinformation is spreading these days, this kind of data is useful to understand the growing role of platforms and the media in order to offer solutions to improve people's media literacy. Who is sharing news? What content and what for?</p>
    </div>
    <svg class="page__curve" viewBox="0 0 375 90" preserveAspectRatio="none" aria-hidden="true">
      <path d="M0 90 C140 88 280 60 375 0 L375 90 Z" fill="var(--purple)"/>
    </svg>
    <span class="page__num" style="right:20px">7</span>
  </article>
</section>

</body>
</html>
```